full stationary design for a modern sleek design company

we are a design company that does modern minimalistic interior design works as well as other design services for high end clients.
we need a full stationary design including and not limited to (double sided business card, letter head, envelopes, documents folder...etc) that reflects the modern style design we do.
sleek modern and minimalistic is the requirements.
Updates

please use the latest attached files as there was a slight modification on the logo Added Wednesday, March 1, 2017

minor update on the logo files in JPG and PSD has been updated kindly follow the new attachments. Added Thursday, March 2, 2017

Target Market(s)

modern minimalist clients

Industry/Entity Type

Design Agency

Requirements
Must have
• the logo
Nice to have
• i like the colors in the colored 3D logo attached
Should not have
• too many colors

```html
<!DOCTYPE html>
<html lang="en">
<head>
<meta charset="utf-8">
<title>Linea Atelier – Business Card</title>
<link href="https://fonts.googleapis.com/css2?family=Open+Sans:wght@400;600;700&display=swap" rel="stylesheet">
<style>
  :root{
    --backdrop:#5b4b3d;
    --charcoal:#333434;
    --orange:#f7931e;
    --white:#ffffff;
    --ink:#3a3b3c;
  }
  html,body{margin:0;padding:0;overflow:hidden}
  body{width:1200px;height:987px;background:var(--backdrop);position:relative;font-family:"Open Sans",Arial,sans-serif}
  .card{position:absolute;left:293px;width:615px;height:352px;border-radius:22px;overflow:hidden;box-shadow:0 3px 8px rgba(0,0,0,.35)}
  .card--front{top:130px}
  .card--back{top:505px;background:var(--orange)}
  .card__shape{position:absolute;inset:0}
  .contact{position:absolute;left:35px;top:72px;color:var(--white)}
  .contact__name{margin:0;font-size:21px;font-weight:700;color:var(--orange);letter-spacing:.2px}
  .contact__role{margin:0 0 14px;font-size:16px}
  .contact__address{margin:0 0 8px;font-size:16px;line-height:23px}
  .contact__list{list-style:none;margin:0;padding:0;font-size:16px;line-height:23.5px}
  .contact__list li{display:flex;align-items:center;gap:8px}
  .contact__list svg{width:15px;height:15px;flex:none}
  .wordmark{position:absolute;display:flex;align-items:center;gap:12px;font-weight:600;text-transform:uppercase;letter-spacing:3px;color:var(--ink);white-space:nowrap}
  .wordmark__square{width:22px;height:22px;background:var(--orange)}
  .card--front .wordmark{left:318px;top:160px;font-size:22px}
  .card--back .wordmark{left:50%;top:50%;transform:translate(-50%,-50%);font-size:36px;letter-spacing:5px}
  .card--back .wordmark__square{width:34px;height:34px;background:var(--ink)}
</style>
</head>
<body>
  <section class="card card--front">
    <svg class="card__shape" viewBox="0 0 615 352" aria-hidden="true">
      <rect width="615" height="352" fill="var(--charcoal)"/>
      <circle cx="480" cy="176" r="218" fill="var(--orange)"/>
      <circle cx="480" cy="176" r="213" fill="var(--white)"/>
      <circle cx="484" cy="176" r="211" fill="var(--white)"/>
    </svg>
    <div class="contact">
      <h1 class="contact__name">MARC DELORME</h1>
      <p class="contact__role">CEO&amp;Founder</p>
      <p class="contact__address">412 Cedar Hollow Road<br>Fairbanks, Alaska 99701</p>
      <ul class="contact__list">
        <li><svg viewBox="0 0 16 16"><path fill="var(--orange)" d="M3 1l3 3-2 2c1 2 3 4 5 5l2-2 3 3-2 3C6 15 1 10 1 3z"/></svg>(555) 214 7730</li>
        <li><svg viewBox="0 0 16 16"><rect x="4" y="1" width="8" height="14" rx="1.5" fill="none" stroke="var(--orange)" stroke-width="1.8"/><rect x="7" y="12" width="2" height="1.5" fill="var(--orange)"/></svg>(555) 903 4418</li>
        <li><svg viewBox="0 0 16 16"><rect x="1" y="3" width="14" height="10" fill="var(--orange)"/><path d="M1 3l7 6 7-6" fill="none" stroke="var(--charcoal)" stroke-width="1.2"/></svg>marc@lineaatelier.com</li>
        <li><svg viewBox="0 0 16 16"><circle cx="8" cy="8" r="7" fill="var(--orange)"/><path d="M5 4c2 1 1 3 3 3s1 3 3 4M4 10c1-1 2 0 3 1" fill="none" stroke="var(--charcoal)" stroke-width="1.2"/></svg>www.lineaatelier.com</li>
      </ul>
    </div>
    <div class="wordmark"><span class="wordmark__square"></span>Linea Atelier</div>
  </section>

  <section class="card card--back">
    <div class="wordmark"><span class="wordmark__square"></span>Linea Atelier</div>
  </section>
</body>
</html>
```